Business Card Design Project : Ridgeline Press

In preparation for market launch, Tamarind's Ridgeline Press require the development of a business card. Ridgeline Press is a Community online publishing web portal. We provide the the city of Whistler located in B.C. (Canada) business directories, News, Classified ads, News, Events and blogs etc.

The main focus of the brand is to help local businesses to corporate with their online advertisement and marketing. Meeting our clients face to face is a must (B2B).

Target Market(s)

The target market is B2B customers. Business Owners to Marketing, advertising Managers

Industry/Entity Type

Business

Requirements
Must have
• - The business card will be two sided.
the BACK side will have our logo which consist of (icon, url,slogan) submited. The logo will be middle and centred.

The FRONT side should have company details:

Company Legal Name: TAMARIND RIDGELINE MEDIA

Owen Farsk
Director of Sales & Marketing

www.tamarindridgeline.biz
owen@tamarindridgeline.biz

Phone: 604 317 8842
#2714 - 582 E. Halvern St.
Vancouver, B.C. V7K2R4 Canada
Nice to have
• - For the "FRONT" side of our business card. You can separate or re-arrange with our logo components (icon, logo,slogan). It does not have to be together.

Also our company legal name is rather long so arrange or organize the name in a way to make it shorter. Your experience and creativity will have to come in play.
Should not have
• should not have other colors beside logo color and black text (2 colors). Also nothing Three dimensional

```html
<!DOCTYPE html>
<html lang="en">
<head>
<meta charset="utf-8">
<title>Tamarind Ridgeline Media – Business Cards</title>
<link rel="stylesheet" href="https://fonts.googleapis.com/css2?family=Open+Sans:wght@400;600;700&display=swap">
<style>
  :root {
    --brand-blue: #1f78c1;
    --ink: #1a1a1a;
    --paper: #ffffff;
    --backdrop: #eceff2;
  }
  * { box-sizing: border-box; margin: 0; padding: 0; }
  html, body { width: 1200px; height: 900px; overflow: hidden; }
  body {
    background: var(--backdrop);
    font-family: "Open Sans", Arial, sans-serif;
    display: flex;
    flex-direction: column;
    align-items: center;
    justify-content: center;
    gap: 44px;
  }
  .card {
    position: relative;
    width: 600px;
    height: 343px;
    background: var(--paper);
    overflow: hidden;
    box-shadow: 0 2px 10px rgba(0,0,0,0.12);
  }
  .card__band { position: absolute; inset: 0; width: 100%; height: 100%; }
  .card__band path { fill: var(--brand-blue); }

  .brand { position: absolute; }
  .brand__name {
    display: flex; align-items: center; gap: 10px;
    font-weight: 700; color: var(--ink); letter-spacing: -0.3px;
    white-space: nowrap;
  }
  .brand__square { width: 16px; height: 16px; background: var(--brand-blue); flex: none; }
  .brand__slogan { color: var(--brand-blue); font-weight: 400; }

  /* back side */
  .card--back .brand { left: 110px; top: 118px; }
  .card--back .brand__name { font-size: 27px; }
  .card--back .brand__slogan { font-size: 19px; margin: 2px 0 0 26px; }
  .card--back .card__url {
    position: absolute; right: 34px; bottom: 30px;
    color: var(--paper); font-size: 14px;
  }

  /* front side */
  .card--front .brand { left: 34px; top: 46px; }
  .card--front .brand__name { font-size: 20px; }
  .card--front .brand__slogan { font-size: 15px; margin: 2px 0 0 26px; }
  .person { position: absolute; right: 34px; top: 34px; text-align: right; }
  .person__name { color: var(--brand-blue); font-weight: 700; font-size: 17px; }
  .person__role { color: var(--ink); font-weight: 600; font-size: 12px; }
  .card--front .card__url {
    position: absolute; right: 34px; top: 160px;
    color: var(--paper); font-size: 13px;
  }
  .contact {
    position: absolute; left: 34px; bottom: 26px;
    list-style: none; color: var(--paper); font-size: 13px; line-height: 1.45;
  }
  .contact li { display: flex; align-items: flex-start; gap: 9px; }
  .contact svg { width: 12px; height: 12px; margin-top: 3px; fill: var(--paper); flex: none; }
  .contact .contact__spacer { width: 12px; flex: none; }
</style>
</head>
<body>

  <section class="card card--back" aria-label="Card back">
    <svg class="card__band" viewBox="0 0 600 343" preserveAspectRatio="none" aria-hidden="true">
      <path d="M0,343 C220,335 470,270 600,110 L600,343 Z"/>
    </svg>
    <div class="brand">
      <div class="brand__name"><span class="brand__square"></span>TAMARIND RIDGELINE MEDIA</div>
      <div class="brand__slogan">Your information gateway</div>
    </div>
    <div class="card__url">www.tamarindridgeline.biz</div>
  </section>

  <section class="card card--front" aria-label="Card front">
    <svg class="card__band" viewBox="0 0 600 343" preserveAspectRatio="none" aria-hidden="true">
      <path d="M0,343 L0,205 C140,198 230,165 300,128 C380,86 470,112 600,72 L600,343 Z"/>
    </svg>
    <div class="brand">
      <div class="brand__name"><span class="brand__square"></span>TAMARIND RIDGELINE MEDIA</div>
      <div class="brand__slogan">Your information gateway</div>
    </div>
    <div class="person">
      <div class="person__name">OWEN FARSK</div>
      <div class="person__role">Director of Sales &amp; Marketing</div>
    </div>
    <div class="card__url">www.tamarindridgeline.biz</div>
    <ul class="contact">
      <li>
        <svg viewBox="0 0 12 12" aria-hidden="true"><path d="M6 1 L11.5 6 H10 V11 H7.2 V8 H4.8 V11 H2 V6 H0.5 Z"/></svg>
        <span>#2714 - 582 E. Halvern St.</span>
      </li>
      <li><span class="contact__spacer"></span><span>Vancouver, B.C. V7K2R4 Canada</span></li>
      <li>
        <svg viewBox="0 0 12 12" aria-hidden="true"><path d="M2.6 0.8 L4.4 3.3 L3.4 4.6 C4 6 5.9 7.9 7.4 8.6 L8.7 7.6 L11.2 9.4 L10 11.2 C5.6 11 1 6.4 0.8 2 Z"/></svg>
        <span>604 317 8842</span>
      </li>
      <li>
        <svg viewBox="0 0 12 12" aria-hidden="true"><path d="M0.5 2.5 H11.5 V9.5 H0.5 Z M1.2 3.1 L6 6.6 L10.8 3.1 V3 H1.2 Z" fill-rule="evenodd"/></svg>
        <span>owen@tamarindridgeline.biz</span>
      </li>
    </ul>
  </section>

</body>
</html>
```